LEARN Business Skills so you can Earn a good living

size of the poster is 8”x 10.75" plus 0.25" bleed.
Please leave 1 inch on the bottoum for footer
I want a design a poster that will attract people's attention.
I appreciate a creative ad however the ad should not take away from being able to clearly read the text.
-I also appreciate a simple creative ad that is not too busy.
-you can use graphics, vectors, or pictures of real people.
-however, if you use real people it should be a white male that is wearing a white shirt and look like a professional person.

Target Market(s)

Potential young business people

Industry/Entity Type

education

Requirements
Must have
• easy to read the text
Nice to have
• I would like a "creative" simple ad that is easy to be read
Should not have
• pictures of women

```html
<!DOCTYPE html>
<html lang="en">
<head>
<meta charset="utf-8">
<title>Learn to Earn – Business Enrichment Course</title>
<link href="https://fonts.googleapis.com/css2?family=Jost:wght@400;500;600;700&display=swap" rel="stylesheet">
<style>
  :root {
    --brand-red: #a52a33;
    --accent-red: #b5252f;
    --ink: #111111;
    --paper: #ffffff;
    --backdrop: #e9e9eb;
    --art-light: #c7434b;
    --art-dark: #7e1f27;
  }
  * { margin: 0; padding: 0; box-sizing: border-box; }
  html, body {
    width: 1200px; height: 1200px; overflow: hidden;
    background: var(--backdrop);
    font-family: "Jost", "Futura", sans-serif;
  }
  .poster {
    position: absolute; left: 212px; top: 50px;
    width: 775px; height: 1100px;
    background: var(--paper);
    overflow: hidden;
  }
  .hero {
    position: absolute; left: 0; top: 0; width: 100%; height: 574px;
    background: var(--brand-red); color: var(--paper);
  }
  .headline-learn {
    position: absolute; left: 84px; top: 92px;
    font-size: 126px; font-weight: 600; line-height: 1; letter-spacing: -4px;
  }
  .headline-earn {
    position: absolute; left: 172px; top: 228px;
    font-weight: 600; line-height: 1; white-space: nowrap;
  }
  .headline-earn .to { font-size: 56px; letter-spacing: -1px; }
  .headline-earn .earn { font-size: 92px; letter-spacing: -2px; margin-left: 12px; }
  .course-name {
    position: absolute; left: 490px; top: 128px;
    font-size: 39px; font-weight: 600; line-height: 1.05;
  }
  .tagline {
    position: absolute; left: 86px; top: 410px;
    font-size: 28px; font-weight: 500; line-height: 1.55; letter-spacing: 0.3px;
  }
  .classroom-art {
    position: absolute; left: 428px; top: 324px; width: 336px; height: 250px;
  }
  .dot { font-family: Arial, Helvetica, sans-serif; }
  .skills-band {
    position: absolute; left: 0; top: 574px; width: 100%; height: 140px;
    background: var(--ink); color: var(--paper);
  }
  .skills-title { position: absolute; left: 46px; top: 18px; font-weight: 500; }
  .skills-title .small { font-size: 21px; }
  .skills-title .big {
    font-size: 66px; font-weight: 600; color: var(--accent-red);
    letter-spacing: -1px; line-height: 1;
  }
  .skills-title .row1 { display: flex; align-items: flex-end; gap: 4px; }
  .skills-title .row2 { display: flex; align-items: baseline; gap: 10px; margin-left: 30px; margin-top: -4px; }
  .skills-title .help { font-size: 30px; color: var(--accent-red); font-weight: 500; }
  .benefits {
    position: absolute; left: 364px; top: 22px; list-style: none;
    font-size: 24px; font-weight: 500; line-height: 1.33;
  }
  .benefits .dot { color: var(--accent-red); margin-right: 8px; }
  .course-list {
    position: absolute; left: 0; top: 740px; width: 100%;
    text-align: center; font-size: 18.5px; font-weight: 500;
    line-height: 37px; color: var(--ink);
  }
  .course-list .hl { color: var(--accent-red); }
  .footer-rule {
    position: absolute; left: 0; top: 1021px; width: 100%; height: 3px;
    background: var(--brand-red);
  }
</style>
</head>
<body>
  <main class="poster">
    <section class="hero">
      <div class="headline-learn">LEARN</div>
      <div class="headline-earn"><span class="to">to</span><span class="earn">EARN</span></div>
      <div class="course-name">Business<br>Enrichment<br>Course</div>
      <p class="tagline">A PROVEN SUCCESS OF<br>HELPING PEOPLE<br>IN THEIR LIVELIHOODS</p>
      <svg class="classroom-art" viewBox="0 0 336 250" role="img" aria-label="Illustration of a presenter in a suit at a flip chart with two seated students">
        <defs>
          <linearGradient id="artTone" x1="0" y1="0" x2="0" y2="1">
            <stop offset="0" stop-color="#c7434b"/>
            <stop offset="1" stop-color="#7e1f27"/>
          </linearGradient>
        </defs>
        <rect width="336" height="250" rx="6" fill="url(#artTone)"/>
      </svg>
    </section>

    <section class="skills-band">
      <div class="skills-title">
        <div class="row1"><span class="small">BUSINESS</span><span class="big">SKILLS</span></div>
        <div class="row2"><span class="small">THAT WILL</span><span class="help">HELP YOU</span></div>
      </div>
      <ul class="benefits">
        <li><span class="dot">•</span>GET A QUALITY JOB</li>
        <li><span class="dot">•</span>START/GROW YOUR BUSINESS</li>
        <li><span class="dot">•</span>INCREASE YOUR SALARY</li>
      </ul>
    </section>

    <section class="course-list">
      <div><span class="dot">•</span> <span class="hl">BUSINESS ADMIISTRATION</span> <span class="dot">•</span> SMALL BUSINESS MANAGEMENT</div>
      <div><span class="dot">•</span> <span class="hl">FINANCE <span class="dot">•</span> INVESTMENTS</span> <span class="dot">•</span> COMPUTERS <span class="dot">•</span> <span class="hl">ACCOUNTING</span></div>
      <div><span class="dot">•</span> <span class="hl">SALES MARKETING</span> <span class="dot">•</span> PROJECT MANAGEMENT INTERVIEWING SKILLS</div>
      <div><span class="dot">•</span> <span class="hl">BUSINESS LAW</span> <span class="dot">•</span> NEGOTIATION <span class="dot">•</span> <span class="hl">PUBLIC SPEAKING</span></div>
      <div><span class="dot">•</span> IMPORT/EXPORT &nbsp;<span class="dot">•</span> <span class="hl">INFORMATION TECHNOLOY</span> <span class="dot">•</span> DISTRIBUTION</div>
      <div><span class="dot">•</span> <span class="hl">MARKETING</span> <span class="dot">•</span> LEDGERWISE <span class="dot">•</span> <span class="hl">REAL ESTATE</span> <span class="dot">•</span> HEALTH CARE</div>
      <div><span class="dot">•</span> <span class="hl">MANAGEMENT</span> <span class="dot">•</span> MARKETBAY</div>
    </section>

    <div class="footer-rule"></div>
  </main>
</body>
</html>
```